Brell Stone Company Business Cards

Front and Back Business Card - logo and text setup - cool design. I need workable photoshop or illustrator files so I can setup each employee card with design that is created
Updates

Hi everyone, thank you for the great entries. Please no more white and blue cards - there are so many already - black and silver only now please. thanks!

Target Market(s)

Construction Industry - Facility Managers

Industry/Entity Type

Construction

Contact Information for Business Card

I really like contemporary simplistic looks - clean neat....not opposed to seeing some black backrounds

Requirements
Must have
• Logo/website address with design on front only - www.brellstone-example.com (logo attached)
• Back:
• Name/Title/Company Address/Phone/email address
Nice to have
• Cool design
Should not have
• Nothing gimmicky like Fire or Water - since we are a Fire Protection company - it has all been done

```html
<!DOCTYPE html>
<html lang="en">
<head>
<meta charset="utf-8">
<title>Brell Stone Company – Business Cards</title>
<link href="https://fonts.googleapis.com/css2?family=Arvo:wght@400;700&display=swap" rel="stylesheet">
<style>
  :root {
    --black: #161718;
    --charcoal: #2b2d30;
    --silver: #a9adb2;
    --silver-light: #d4d7da;
    --ink: #3a3c3f;
    --rule: #c4c7ca;
    --paper: #f6f6f7;
    --stage: #e6e6e6;
  }
  * { box-sizing: border-box; margin: 0; padding: 0; }
  html, body { width: 1200px; height: 900px; overflow: hidden; }
  body {
    background: var(--stage);
    font-family: "Arvo", Georgia, serif;
    display: flex;
    align-items: center;
    justify-content: center;
    gap: 44px;
  }

  /* ---------- Front card (portrait) ---------- */
  .card-front {
    width: 340px;
    height: 556px;
    background: var(--paper);
    border: 9px solid var(--silver);
    padding: 34px 30px 34px;
    display: flex;
    flex-direction: column;
    justify-content: space-between;
    color: var(--ink);
  }
  .brand-name {
    font-weight: 700;
    font-size: 31px;
    line-height: 1;
    color: var(--black);
    letter-spacing: -0.5px;
  }
  .person-icon { display: block; margin: 0 0 6px 84px; }
  .person-name {
    font-size: 28px;
    line-height: 1.05;
    color: var(--black);
    letter-spacing: 1px;
  }
  .person-name .given { color: var(--silver); }
  .person-title {
    font-size: 15px;
    margin-top: 3px;
  }
  .person-title .accent { color: #8a8e93; }
  .rule {
    border: 0;
    border-top: 1px solid var(--rule);
  }
  .contact-list { list-style: none; }
  .contact-list li {
    display: flex;
    align-items: center;
    gap: 12px;
    font-size: 14.5px;
    line-height: 1.8;
  }
  .contact-list svg { flex: none; }
  .address {
    text-align: center;
    font-size: 17px;
    line-height: 1.35;
  }
  .address svg { display: block; margin: 0 auto 10px; }

  /* ---------- Back card (landscape) ---------- */
  .card-back {
    width: 556px;
    height: 340px;
    background: linear-gradient(160deg, var(--charcoal), var(--black));
    position: relative;
  }
  .back-url {
    position: absolute;
    left: 70px;
    bottom: 70px;
    color: var(--silver-light);
    font-size: 13px;
    letter-spacing: 5px;
  }
</style>
</head>
<body>

  <section class="card-front" aria-label="Front of business card">
    <div class="brand-name">brellstone inc.</div>

    <div class="person">
      <svg class="person-icon" width="16" height="18" viewBox="0 0 16 18" aria-hidden="true">
        <circle cx="8" cy="5" r="4" fill="var(--black)"/>
        <path d="M0 18 Q0 10 8 10 Q16 10 16 18 Z" fill="var(--black)"/>
      </svg>
      <div class="person-name"><span class="given">MARCUS</span> HALE</div>
      <div class="person-title">CEO of <span class="accent">brellstone.inc</span></div>
    </div>

    <hr class="rule">

    <ul class="contact-list">
      <li>
        <svg width="16" height="14" viewBox="0 0 16 14" aria-hidden="true">
          <path d="M1 4 Q8 -1 15 4 L13 6 L11 4 L5 4 L3 6 Z" fill="var(--black)"/>
          <rect x="3" y="7" width="10" height="7" rx="1.5" fill="var(--black)"/>
        </svg>
        (02) 5550 1234
      </li>
      <li>
        <svg width="16" height="12" viewBox="0 0 16 12" aria-hidden="true">
          <rect width="16" height="12" rx="1" fill="var(--black)"/>
          <path d="M0.5 1 L8 7 L15.5 1" stroke="#fff" stroke-width="1.3" fill="none"/>
        </svg>
        info@brellstone-example.com
      </li>
      <li>
        <svg width="16" height="16" viewBox="0 0 16 16" aria-hidden="true">
          <circle cx="8" cy="8" r="7.5" fill="var(--black)"/>
          <ellipse cx="8" cy="8" rx="3" ry="7" stroke="#fff" stroke-width="1" fill="none"/>
          <path d="M1 8 H15" stroke="#fff" stroke-width="1"/>
        </svg>
        www.brellstone-example.com
      </li>
    </ul>

    <hr class="rule">

    <div class="address">
      <svg width="14" height="19" viewBox="0 0 14 19" aria-hidden="true">
        <path d="M7 0 A7 7 0 0 1 14 7 C14 12 7 19 7 19 C7 19 0 12 0 7 A7 7 0 0 1 7 0 Z" fill="var(--black)"/>
        <circle cx="7" cy="7" r="2.6" fill="#fff"/>
      </svg>
      18/4 Quarry Lane, Northvale<br>NSW 2090, NY
    </div>

    <hr class="rule">
  </section>

  <section class="card-back" aria-label="Back of business card">
    <div class="back-url">www.brellstone-example.com</div>
  </section>

</body>
</html>
```